Business Card for Professional Photographer

I'm looking for an eye catching modern clean design that compliments my logo/ website fonts & colours.
I specialise in architecture, corporate & commercial photography so I'm marketing to professional clients rather than portrait / wedding clients.

I would prefer to not have a solid black design.

My logo brand guide is as follows :

Main front font. : Reislust
Main font colour : #fff
Slogan front font : Ubuntu Bold
Monogram front font : Venti Medium
Container colour : #fff

I need print ready files in pdf .png & .eps formats.

Included in the files below are some screen grabs as reference to font & colours etc.

```html
<!DOCTYPE html>
<html lang="en">
<head>
<meta charset="utf-8">
<title>Northlight Frame – Business Card</title>
<link rel="stylesheet" href="https://fonts.googleapis.com/css2?family=Open+Sans:wght@300;400;700&display=swap">
<style>
  :root {
    --backdrop: #3b3430;
    --card: #262626;
    --card-back: #1f1f1f;
    --pattern: #2a2a2a;
    --gold: #d4a62a;
    --white: #ffffff;
    --muted: #e8e8e8;
  }
  * { margin: 0; padding: 0; box-sizing: border-box; }
  html, body { width: 1200px; height: 847px; overflow: hidden; }
  body {
    background: var(--backdrop);
    font-family: "Open Sans", Arial, sans-serif;
    position: relative;
  }
  .card {
    position: absolute;
    top: 269px;
    width: 540px;
    height: 309px;
    box-shadow: 0 10px 24px rgba(0,0,0,0.45);
    overflow: hidden;
  }
  .card--back { left: 40px; background: var(--card-back); }
  .card--front { left: 620px; background: var(--card); }

  .back__pattern {
    position: absolute; inset: 0;
    background: linear-gradient(135deg, var(--pattern), var(--card-back));
  }
  .back__wordmark {
    position: absolute;
    left: 0; right: 0; top: 140px;
    text-align: center;
    color: var(--gold);
    font-weight: 300;
    font-size: 18px;
    letter-spacing: 5px;
    text-transform: uppercase;
  }

  .brand {
    position: absolute;
    left: 30px; top: 118px;
    display: flex; align-items: center; gap: 12px;
  }
  .brand__square {
    width: 40px; height: 40px;
    background: var(--gold);
    flex: none;
  }
  .brand__name {
    color: var(--white);
    font-weight: 300;
    font-size: 15px;
    letter-spacing: 3px;
    text-transform: uppercase;
    line-height: 1;
    white-space: nowrap;
  }
  .brand__tagline {
    margin-top: 6px;
    color: var(--gold);
    font-size: 7.5px;
    letter-spacing: 1.4px;
    white-space: nowrap;
  }
  .divider {
    position: absolute;
    left: 318px; top: 92px;
    width: 1.5px; height: 128px;
    background: var(--gold);
  }
  .contact {
    position: absolute;
    left: 334px; top: 96px;
    white-space: nowrap;
  }
  .contact__name {
    color: var(--gold);
    font-weight: 700;
    font-size: 19px;
    text-transform: uppercase;
    line-height: 1.1;
  }
  .contact__role {
    color: var(--white);
    font-size: 13px;
    margin-bottom: 12px;
  }
  .contact__list { list-style: none; }
  .contact__item {
    display: flex; align-items: center; gap: 6px;
    color: var(--muted);
    font-size: 12.5px;
    line-height: 1.55;
  }
  .contact__icon { width: 10px; height: 10px; flex: none; fill: var(--gold); }
</style>
</head>
<body>
  <section class="card card--back" aria-label="Card back">
    <div class="back__pattern" role="img" aria-label="Tonal embossed repeat of the studio mark across the card back"></div>
    <div class="back__wordmark">Northlight Frame</div>
  </section>

  <section class="card card--front" aria-label="Card front">
    <div class="brand">
      <div class="brand__square"></div>
      <div>
        <div class="brand__name">Northlight Frame</div>
        <div class="brand__tagline">Architecture Corporate Commercial</div>
      </div>
    </div>

    <div class="divider"></div>

    <div class="contact">
      <div class="contact__name">Daniel Averly</div>
      <div class="contact__role">Director</div>
      <ul class="contact__list">
        <li class="contact__item">
          <svg class="contact__icon" viewBox="0 0 24 24"><path d="M6.6 10.8a15 15 0 0 0 6.6 6.6l2.2-2.2a1 1 0 0 1 1-.25 11.4 11.4 0 0 0 3.6.57 1 1 0 0 1 1 1V20a1 1 0 0 1-1 1A17 17 0 0 1 3 4a1 1 0 0 1 1-1h3.5a1 1 0 0 1 1 1c0 1.25.2 2.45.57 3.57a1 1 0 0 1-.25 1z"/></svg>
          555 014 2290
        </li>
        <li class="contact__item">
          <svg class="contact__icon" viewBox="0 0 24 24"><path d="M2 5h20v2l-10 6L2 7z"/><path d="M2 9l10 6 10-6v10H2z"/></svg>
          hello@northlightframe.com
        </li>
        <li class="contact__item">
          <svg class="contact__icon" viewBox="0 0 24 24"><circle cx="12" cy="12" r="10"/></svg>
          www.northlightframe.com
        </li>
      </ul>
    </div>
  </section>
</body>
</html>
```